RWT Fittings Ltd Business Cards

We need a business card with our business logo. We provide window and door installations on high-rises in west coast British Colombia, Canada.

I would like my business information and details on one side of the card, and the other side the company name with logo

Target Market(s)

General Contractors

Industry/Entity Type

Construction

Contact Information for Business Card

one side i want my company name and logo in the dark theme logo that i provided

Requirements
Must have
• Marco Peltieri, 16045518293, RWTFittings@mailbox-demo.com, 1407-5194 Linden Row Burnaby BC, V5H 2K9, Owner & Manager

```html
<!DOCTYPE html>
<html lang="en">
<head>
<meta charset="UTF-8">
<title>RWT Fittings Ltd – Business Cards</title>
<link href="https://fonts.googleapis.com/css2?family=Roboto:wght@400;500;700;900&display=swap" rel="stylesheet">
<style>
  :root {
    --sky: #27a8e1;
    --ink: #111214;
    --card-dark: #1d1d20;
    --text-light: #f2f2f2;
    --muted: #8a8a8e;
    --page: #2a2a2d;
  }
  * { box-sizing: border-box; margin: 0; padding: 0; }
  html, body {
    width: 1200px; height: 780px; overflow: hidden;
    background: var(--page);
    font-family: "Roboto", Arial, sans-serif;
  }
  .sheet {
    position: relative; width: 1200px; height: 780px;
    display: flex; align-items: center; justify-content: center; gap: 40px;
  }
  .card {
    position: relative; width: 540px; height: 310px;
    border-radius: 22px; overflow: hidden;
  }
  /* Front side */
  .card--front {
    background: var(--sky);
    display: flex; align-items: center; justify-content: center;
  }
  .brand {
    display: flex; align-items: center; gap: 16px;
  }
  .brand__mark {
    width: 34px; height: 34px; background: var(--ink);
  }
  .brand__name {
    font-weight: 900; font-size: 44px; letter-spacing: 0.5px;
    color: var(--ink); text-transform: uppercase; line-height: 1;
  }
  /* Back side */
  .card--back {
    background: var(--card-dark);
    border: 3px solid var(--sky);
  }
  .accent-bar {
    position: absolute; top: 0; right: 22px; width: 12px; height: 58px;
    background: var(--sky);
  }
  .person {
    position: absolute; top: 18px; right: 46px; text-align: right;
  }
  .person__name {
    font-weight: 700; font-size: 28px; color: var(--sky); line-height: 1.1;
  }
  .person__role {
    font-weight: 500; font-size: 13px; color: var(--text-light); margin-top: 2px;
  }
  .back-brand {
    position: absolute; left: 34px; top: 112px;
    display: flex; align-items: center; gap: 10px;
  }
  .back-brand .brand__mark { width: 20px; height: 20px; background: var(--sky); }
  .back-brand .brand__name { font-size: 26px; color: var(--sky); }
  .decoration {
    position: absolute; right: 0; top: 72px; width: 230px; height: 232px;
    background: linear-gradient(135deg, #2b2b2f 0%, #141416 70%);
    border-radius: 0 0 18px 0;
  }
  .contact {
    position: absolute; left: 34px; bottom: 26px;
    color: var(--text-light); font-size: 13.5px; line-height: 1.45;
  }
  .contact__address { margin-bottom: 8px; }
  .contact__row { display: flex; align-items: center; gap: 8px; }
  .contact__icon { width: 13px; height: 13px; flex: none; }
</style>
</head>
<body>
<main class="sheet">
  <section class="card card--front" aria-label="Front of card">
    <div class="brand">
      <span class="brand__mark"></span>
      <span class="brand__name">RWT Fittings Ltd</span>
    </div>
  </section>

  <section class="card card--back" aria-label="Back of card">
    <div class="accent-bar"></div>
    <div class="person">
      <p class="person__name">Marco Peltieri</p>
      <p class="person__role">Owner &amp; Manager</p>
    </div>

    <div class="back-brand">
      <span class="brand__mark"></span>
      <span class="brand__name">RWT Fittings Ltd</span>
    </div>

    <div class="decoration" role="img" aria-label="Large tonal brand emblem in glossy black"></div>

    <div class="contact">
      <p class="contact__address">1407-5194 Linden Row<br>Burnaby BC, V5H 2K9</p>
      <p class="contact__row">
        <svg class="contact__icon" viewBox="0 0 24 24" aria-hidden="true"><path fill="#27a8e1" d="M6.6 10.8a15.1 15.1 0 0 0 6.6 6.6l2.2-2.2c.3-.3.7-.4 1-.2 1.1.4 2.3.6 3.6.6.6 0 1 .4 1 1V20c0 .6-.4 1-1 1A17 17 0 0 1 3 4c0-.6.4-1 1-1h3.5c.6 0 1 .4 1 1 0 1.3.2 2.5.6 3.6.1.3 0 .7-.2 1z"/></svg>
        1604 551 8293
      </p>
      <p class="contact__row">
        <svg class="contact__icon" viewBox="0 0 24 24" aria-hidden="true"><rect x="2" y="5" width="20" height="14" rx="2" fill="#27a8e1"/><path d="M3 6l9 7 9-7" stroke="#1d1d20" stroke-width="2" fill="none"/></svg>
        RWTFittings@mailbox-demo.com
      </p>
    </div>
  </section>
</main>
</body>
</html>
```